ro dun magazine

just need coupons of real customers made for my magazine, I have the layout or temp lets of the magazine i just need the coupons to be made and plug-in. i have examples, of the ads or coupons, I'm sure they will need to redone. and in a section of the magazine their in a church directory. with this section , i need the pic of the pastor plug in with their church information and in do have some ex-samples of that as well. with the websites of the businesses. if you need to grab an image from their site . you'll be able to do so. all of the business are in the upload section , these are small base business so a lot of the ads and logos need redone any way . so i will look at it and let you know.

P.S with the new coupons and logos I'm trying to impress these customers to stay with the magazine

Target Market(s)

small businesses

Requirements
Must have
• good graphics
Should not have
• not pixelated graphics

```html
<!DOCTYPE html>
<html lang="en">
<head>
<meta charset="utf-8">
<title>Hourline – Business Card</title>
<link rel="stylesheet" href="https://fonts.googleapis.com/css2?family=Arimo:wght@400;700&display=swap">
<style>
  :root {
    --backdrop: #808080;
    --card: #ffffff;
    --ink: #231f20;
    --mark: #000000;
  }
  * { margin: 0; padding: 0; box-sizing: border-box; }
  html, body {
    width: 1200px;
    height: 1200px;
    overflow: hidden;
    background: var(--backdrop);
  }
  .business-card {
    position: absolute;
    left: 59px;
    top: 315px;
    width: 1082px;
    height: 612px;
    background: var(--card);
  }
  .brand-row {
    position: absolute;
    left: 0;
    top: 0;
    width: 1082px;
    height: 612px;
  }
  .brand-name {
    font-family: "Arimo", Arial, sans-serif;
    font-weight: 700;
    font-size: 119px;
    fill: var(--ink);
  }
  .contact-details {
    position: absolute;
    left: 391px;
    top: 348px;
    width: 400px;
    text-align: center;
    font-family: "Arimo", Arial, sans-serif;
    font-weight: 400;
    font-size: 43px;
    line-height: 46px;
    color: var(--ink);
  }
</style>
</head>
<body>
  <main class="business-card">
    <svg class="brand-row" viewBox="0 0 1082 612" xmlns="http://www.w3.org/2000/svg">
      <circle class="brand-circle" cx="125" cy="281" r="79.5" fill="none" stroke="var(--mark)" stroke-width="17"/>
      <text class="brand-name" x="245" y="323" textLength="789" lengthAdjust="spacing">HOURLINE</text>
    </svg>
    <address class="contact-details" style="font-style: normal;">
      <div class="phone">1 (800) 555-0147</div>
      <div class="street">4815 Marlow street</div>
      <div class="city">Aldenville,PA 15990</div>
    </address>
  </main>
</body>
</html>
```